Business Card front and back

I am looking for business card design. I really really like the design file I uploaded named 627788_19250069_3478263_85f427ee_image

Target Market(s)

Corporate Fitness High end Private country club

Industry/Entity Type

Fitness Industry

Contact Information for Business Card

The last image I like as an example I uploaded a bunch of my logos. The file labeled "the signature" is my business card information for you to use

Colors
0054AA
0677BA
7BADD7
CADEEF
E8F1F8

Requirements
Must have
• E-mail sigThe file I uploaded labeled "627788_19250069_3478263_85f427ee_image" with all the plus signs on the back if those could be the logo symbol I uploaded labeled "1 back.png"

```html
<!DOCTYPE html>
<html lang="en">
<head>
<meta charset="utf-8">
<title>Summit Form Studio – Business Card</title>
<link href="https://fonts.googleapis.com/css2?family=Poppins:wght@400;500&family=Orbitron:wght@800&display=swap" rel="stylesheet">
<style>
  :root{
    --backdrop:#2c2c2c;
    --card:#0c0c0d;
    --card-pattern-a:#1a1a1b;
    --card-pattern-b:#121213;
    --mark-a:#3a3a3c;
    --mark-b:#050505;
    --blue:#4a86cf;
    --white:#f2f2f2;
  }
  *{margin:0;padding:0;box-sizing:border-box}
  html,body{width:1200px;height:1015px;overflow:hidden;background:var(--backdrop)}
  body{position:relative;font-family:"Poppins",sans-serif;color:var(--white)}
  .card{
    position:absolute;left:250px;width:700px;height:400px;
    background:var(--card);overflow:hidden;
    box-shadow:0 14px 30px rgba(0,0,0,.45);
  }
  .card--front{top:70px}
  .card--back{top:545px}

  .pattern-field{
    position:absolute;inset:0;
    background:linear-gradient(135deg,var(--card-pattern-a),var(--card-pattern-b));
  }
  .front-content{
    position:relative;height:100%;
    display:flex;flex-direction:column;align-items:center;justify-content:center;
    text-align:center;
  }
  .brand{display:flex;align-items:center;gap:12px;margin-bottom:26px}
  .brand-square{width:26px;height:26px;background:var(--blue)}
  .brand-name{font-size:26px;font-weight:500;letter-spacing:2px;color:var(--white);text-transform:uppercase}
  .offerings-title{font-size:22px;font-weight:400;color:var(--blue);margin-bottom:6px}
  .offerings-list{list-style:none;font-size:17px;line-height:1.45}

  .contact{position:absolute;left:70px;top:95px}
  .person-name{font-family:"Orbitron",sans-serif;font-weight:800;font-size:27px;color:var(--blue);letter-spacing:1px}
  .person-role{font-size:17px;margin-top:2px}
  .details{list-style:none;margin-top:44px;font-size:16px}
  .details li{display:flex;align-items:center;gap:12px;height:27px}
  .details li.location{margin-top:10px}
  .details svg{width:18px;height:18px;fill:var(--blue);flex:none}
  .mark-area{
    position:absolute;right:40px;top:50px;width:290px;height:300px;
    background:radial-gradient(circle at 75% 25%,var(--mark-a),var(--mark-b) 70%);
    border-radius:8px;
  }
</style>
</head>
<body>

<section class="card card--front">
  <div class="pattern-field" role="img" aria-label="Repeating faint brand symbol pattern across the card"></div>
  <div class="front-content">
    <div class="brand">
      <span class="brand-square"></span>
      <span class="brand-name">Summit Form Studio</span>
    </div>
    <h2 class="offerings-title">Offerings</h2>
    <ul class="offerings-list">
      <li>Conceptual Planning &nbsp;-&nbsp; Equipment Specifications</li>
      <li>Equipment Procurement &nbsp;-&nbsp; 3rd Party Collaboration</li>
      <li>Preventative Maintenance Service</li>
    </ul>
  </div>
</section>

<section class="card card--back">
  <div class="contact">
    <h1 class="person-name">DALEN MOOR</h1>
    <p class="person-role">Principal</p>
    <ul class="details">
      <li>
        <svg viewBox="0 0 24 24"><path d="M6.6 10.8a15 15 0 0 0 6.6 6.6l2.2-2.2a1 1 0 0 1 1-.25 11.4 11.4 0 0 0 3.6.57 1 1 0 0 1 1 1V20a1 1 0 0 1-1 1A17 17 0 0 1 3 4a1 1 0 0 1 1-1h3.5a1 1 0 0 1 1 1c0 1.250.2 2.450.57 3.6a1 1 0 0 1-.25 1z"/></svg>
        <span>555-014-2277</span>
      </li>
      <li>
        <svg viewBox="0 0 24 24"><path d="M2 5h20v14H2zm2 2v.5l8 5 8-5V7l-8 5z"/></svg>
        <span>dalen@summitformstudio.co</span>
      </li>
      <li>
        <svg viewBox="0 0 24 24"><path d="M12 2a10 10 0 1 0 0 20 10 10 0 0 0 0-20zm6.9 6h-3a15 15 0 0 0-1.3-3.9A8 8 0 0 1 18.9 8zM12 4c.8 1.1 1.5 2.5 1.9 4h-3.8c.4-1.5 1.1-2.9 1.9-4zM4.3 14a8 8 0 0 1 0-4h3.4a16 16 0 0 0 0 4zm.8 2h3a15 15 0 0 0 1.3 3.9A8 8 0 0 1 5.1 16zm3-8h-3a8 8 0 0 1 4.3-3.9A15 15 0 0 0 8.1 8zM12 20c-.8-1.1-1.5-2.5-1.9-4h3.8c-.4 1.5-1.1 2.9-1.9 4zm2.3-6H9.7a14 14 0 0 1 0-4h4.6a14 14 0 0 1 0 4zm.3 5.9a15 15 0 0 0 1.3-3.9h3a8 8 0 0 1-4.3 3.9zm1.7-5.9a16 16 0 0 0 0-4h3.4a8 8 0 0 1 0 4z"/></svg>
        <span>www.summitformstudio.co</span>
      </li>
      <li class="location">
        <svg viewBox="0 0 24 24"><path d="M12 2a7 7 0 0 0-7 7c0 5.2 7 13 7 13s7-7.8 7-13a7 7 0 0 0-7-7zm0 9.5A2.5 2.5 0 1 1 12 6.5a2.5 2.5 0 0 1 0 5z"/></svg>
        <span>Northfield Region</span>
      </li>
    </ul>
  </div>
  <div class="mark-area" role="img" aria-label="Large glossy dark brand symbol"></div>
</section>

</body>
</html>
```